Global (re)insurance broker needs a business card design

We need a classic business card for our company that is headquartered in SG, with offices in Malaysia and Dubai. We specialise in insurance and reinsurance broking and consultancy for our global clients.

```html
<!DOCTYPE html>
<html lang="en">
<head>
<meta charset="utf-8">
<title>Korvane Business Card</title>
<link href="https://fonts.googleapis.com/css2?family=Open+Sans:wght@400;700&display=swap" rel="stylesheet">
<style>
  :root {
    --stage: #2a2a2d;
    --card-black: #141414;
    --brand-blue: #274b9b;
    --brand-green: #c5dcb7;
    --text-white: #ffffff;
  }
  * { margin: 0; padding: 0; box-sizing: border-box; }
  html, body {
    width: 1200px; height: 947px; overflow: hidden;
    background: var(--stage);
    font-family: "Open Sans", sans-serif;
  }
  .stage {
    width: 1200px; height: 947px;
    display: flex; flex-direction: column;
    align-items: center; justify-content: center; gap: 36px;
  }
  .card {
    position: relative;
    width: 735px; height: 420px;
    border-radius: 24px;
    overflow: hidden;
    background: var(--card-black);
    box-shadow: 0 14px 30px rgba(0,0,0,0.45);
  }
  .card-background { position: absolute; inset: 0; }
  .wordmark {
    color: var(--brand-green);
    font-weight: 700;
    letter-spacing: 2px;
    line-height: 1;
  }
  .card-front .wordmark {
    position: absolute; inset: 0;
    display: flex; align-items: center; justify-content: center;
    font-size: 116px;
  }
  .card-back .wordmark {
    position: absolute; left: 44px; top: 130px;
    font-size: 62px;
  }
  .identity {
    position: absolute; right: 40px; top: 112px;
    text-align: right; color: var(--text-white);
  }
  .identity .person-name {
    color: var(--brand-green); font-weight: 700; font-size: 30px; line-height: 1.1;
  }
  .identity .person-role { font-size: 18px; margin-top: 2px; }
  .contact-list {
    position: absolute; right: 40px; top: 222px;
    list-style: none; color: var(--text-white);
    font-size: 17px; line-height: 29px; text-align: right;
  }
  .contact-list li { display: flex; align-items: center; justify-content: flex-end; gap: 10px; }
  .contact-list svg { width: 15px; height: 15px; flex: none; }
  .office-address {
    position: absolute; left: 40px; bottom: 22px;
    color: var(--text-white); font-size: 17px; line-height: 24px; font-style: normal;
  }
</style>
</head>
<body>
<main class="stage">
  <section class="card card-front" aria-label="Card front">
    <div class="wordmark">KORVANE</div>
  </section>

  <section class="card card-back" aria-label="Card back">
    <svg class="card-background" viewBox="0 0 735 420" preserveAspectRatio="none" aria-hidden="true">
      <path d="M570 0 C490 30 470 170 410 230 C330 300 160 272 0 292 L0 420 L735 420 L735 0 Z" fill="var(--brand-blue)"/>
      <path d="M570 0 C490 30 470 170 410 230 C330 300 160 272 0 292" fill="none" stroke="var(--card-black)" stroke-width="8"/>
      <path d="M532 10 C462 60 446 170 391 222 C316 284 150 262 0 279" fill="none" stroke="var(--brand-green)" stroke-width="6" stroke-linecap="round"/>
    </svg>

    <div class="wordmark">KORVANE</div>

    <div class="identity">
      <p class="person-name">Mei Lin Koh</p>
      <p class="person-role">Chief Operating Officer</p>
    </div>

    <ul class="contact-list">
      <li>+65 9123 4567
        <svg viewBox="0 0 24 24" aria-hidden="true"><path fill="var(--brand-green)" d="M6.6 10.8a15 15 0 0 0 6.6 6.6l2.2-2.2c.3-.3.7-.4 1-.2 1.1.4 2.3.6 3.6.6.6 0 1 .4 1 1V20c0 .6-.4 1-1 1A17 17 0 0 1 3 4c0-.6.4-1 1-1h3.5c.6 0 1 .4 1 1 0 1.3.2 2.5.6 3.6.1.3 0 .7-.2 1z"/></svg>
      </li>
      <li>meilin@korvane.com
        <svg viewBox="0 0 24 24" aria-hidden="true"><path fill="var(--brand-green)" d="M2 5h20v14H2z"/><path fill="none" stroke="var(--brand-blue)" stroke-width="2" d="M2 5l10 8 10-8"/></svg>
      </li>
      <li>www.korvane.com
        <svg viewBox="0 0 24 24" aria-hidden="true"><circle cx="12" cy="12" r="10" fill="var(--brand-green)"/><path fill="none" stroke="var(--brand-blue)" stroke-width="1.6" d="M2 12h20M12 2c3 3 3 17 0 20M12 2c-3 3-3 17 0 20"/></svg>
      </li>
    </ul>

    <address class="office-address">
      22 Harbour Lane,<br>
      Marina Tower #08-05,<br>
      Singapore 018956
    </address>
  </section>
</main>
</body>
</html>
```